Stationery for Villa Marenta Design Hotel**

Who we are:

Wander on an isolated beach while breathing in the fresh, salty, sea air. Listen to the warm Pacific wind rustling through green palm trees as you walk to a pristine lagoon. Feel the delicious warmth of the sun kiss your skin; the beach is yours. At Villa Marenta you can experience a vacation in undisturbed, natural beauty. We have created a place for you to find new strength, relaxation, and inner harmony. We offer total rest to the experienced traveler from all over the world.

We are a brand new and smartly built design-hotel (under construction) close to a unique beach and a fantastic surf spot in Huatulco, Southwest Mexico.

As you can see in the attachments, we do have an established corporate design, but as for now still need a format for booklets for information around our hotel and things to do in the area, important numbers (we fill in the content for that one).

Our corporate colors:
green #64b445, brown #b07043, blue #0ab7cf, yellow # f9b02a and #fcc01a, navy #444f69
Corporate fonts:
Krub and Miller Banner.
For further information access:
www.villamarenta.example
https://slidevault.example/view/QmPxLwZrTyKsNbVcHdJe/

Social Media: VillaMarenta

Industry/Entity Type

Hotel

Font styles to use
Other font styles liked:
• Krub, Miller Banner

Requirements
Must have
• Stick to Logo Design, defined corporate elements, logo, colors, fonts and general touch and feel
Nice to have
• Who we are:

Our corporate colors:
Corporate fonts:
Krub and Miller Banner.
www.villamarenta.example

Social Media: VillaMarenta

```html
<!DOCTYPE html>
<html lang="en">
<head>
<meta charset="utf-8">
<title>Villa Marenta Design Hotel – Letterhead</title>
<link rel="stylesheet" href="https://fonts.googleapis.com/css2?family=Krub:wght@400;500&family=Open+Sans:wght@400&display=swap">
<style>
  :root {
    --backdrop: #dedede;
    --paper: #f8f8f8;
    --ink: #4a4a4a;
    --ink-dark: #3a3a3a;
    --brand-green: #64b445;
    --brand-yellow: #f9b02a;
    --brand-navy: #444f69;
    --signature-tone: #e6e6e6;
  }
  * { box-sizing: border-box; margin: 0; padding: 0; }
  html, body {
    width: 1153px; height: 1200px; overflow: hidden;
    background: var(--backdrop);
  }
  .letterhead {
    position: absolute;
    left: 160px; top: 20px;
    width: 1008px; height: 1406px;
    background: var(--paper);
    box-shadow: 0 10px 30px rgba(0,0,0,0.12);
    transform: scale(0.825);
    transform-origin: top left;
  }
  .brand {
    position: absolute;
    left: 100px; top: 92px;
    display: flex; align-items: center; gap: 12px;
  }
  .brand-square {
    width: 34px; height: 34px;
    background: var(--brand-yellow);
  }
  .brand-name {
    font-family: "Krub", sans-serif;
    font-weight: 500;
    font-size: 26px;
    color: var(--brand-yellow);
    letter-spacing: 0.5px;
  }
  .contact {
    position: absolute;
    left: 669px; top: 98px;
    font-family: "Krub", sans-serif;
    font-size: 20px;
    line-height: 25px;
    color: var(--ink-dark);
  }
  .contact-address { margin-bottom: 7px; }
  .contact-line { display: flex; align-items: center; gap: 7px; height: 27px; }
  .contact-icon { width: 20px; height: 20px; flex: none; }
  .letter {
    position: absolute;
    left: 90px; top: 364px;
    width: 827px;
    font-family: "Open Sans", sans-serif;
    font-size: 18.5px;
    line-height: 27.2px;
    color: var(--ink);
  }
  .letter p { margin-bottom: 27px; text-align: justify; }
  .letter .salutation, .letter .closing { text-align: left; }
  .signature {
    position: absolute;
    left: 92px; top: 1076px;
    width: 120px; height: 114px;
    background: var(--signature-tone);
  }
</style>
</head>
<body>
  <main class="letterhead">
    <header>
      <div class="brand">
        <span class="brand-square"></span>
        <span class="brand-name">Villa Marenta</span>
      </div>
      <address class="contact" style="font-style:normal">
        <div class="contact-address">Playa Serena, Huatulco<br>Oaxaca, Mexiko</div>
        <div class="contact-line">
          <svg class="contact-icon" viewBox="0 0 20 20"><path fill="var(--brand-green)" d="M4 2l3 0 2 5-2 1.5c1 2.2 2.8 4 5 5l1.5-2 5 2v3c0 1-1 2-2 2C9 18.5 1.5 11 1.5 4c0-1 1-2 2.5-2z"/></svg>
          <span>+52 1 (555) 014 7720</span>
        </div>
        <div class="contact-line">
          <svg class="contact-icon" viewBox="0 0 20 20"><rect x="1" y="4" width="18" height="12" fill="var(--brand-green)"/><path d="M1 4l9 7 9-7" fill="none" stroke="var(--paper)" stroke-width="1.5"/></svg>
          <span>hello@villamarenta.example</span>
        </div>
        <div class="contact-line">
          <svg class="contact-icon" viewBox="0 0 20 20"><circle cx="10" cy="10" r="8" fill="none" stroke="var(--brand-green)" stroke-width="2"/><path d="M2 10h16M10 2c-3 3-3 13 0 16M10 2c3 3 3 13 0 16" fill="none" stroke="var(--brand-green)" stroke-width="1.5"/></svg>
          <span>www.villamarenta.example</span>
        </div>
      </address>
    </header>
    <article class="letter">
      <p class="salutation">Dear customer,</p>
      <p>Lorem ipsum dolor sit amet, consectetur adipisicing elit, sed do eiusmod tempor incididunt ut labore et dolore magna aliqua. Ut enim ad minim veniam, quis nostrud exercitation ullamco laboris nisi ut aliquip ex ea commodo consequat. Duis aute irure dolor in reprehenderit in voluptate velit esse cillum dolore eu fugiat nulla pariatur. Excepteur sint occaecat cupidatat non proident, sunt in culpa qui officia deserunt mollit anim id est laborum.</p>
      <p>Lorem ipsum dolor sit amet, consectetur adipisicing elit, sed do eiusmod tempor incididunt ut labore et dolore magna aliqua. Ut enim ad minim veniam, quis nostrud exercitation ullamco laboris nisi ut aliquip ex ea commodo consequat. Duis aute irure dolor in reprehenderit in voluptate velit esse cillum dolore eu fugiat nulla pariatur. Excepteur sint occaecat cupidatat non proident, sunt in culpa qui officia deserunt mollit anim id est laborum.</p>
      <p>Lorem ipsum dolor sit amet, consectetur adipisicing elit, sed do eiusmod tempor incididunt ut labore et dolore magna aliqua. Ut enim ad minim veniam, quis nostrud exercitation ullamco laboris nisi ut aliquip ex ea commodo consequat. Duis aute irure dolor in reprehenderit in voluptate velit esse cillum dolore eu fugiat nulla pariatur. Excepteur sint occaecat cupidatat non proident, sunt in culpa qui officia deserunt mollit anim id est laborum.</p>
      <p>Lorem ipsum dolor sit amet, consectetur adipisicing elit, sed do eiusmod tempor incididunt ut labore et dolore magna aliqua. Ut enim ad minim veniam, quis nostrud exercitation ullamco laboris nisi ut aliquip ex ea commodo consequat. Duis aute irure dolor in reprehenderit.</p>
      <p class="closing">Yours Sincerely,</p>
    </article>
    <div class="signature" role="img" aria-label="Handwritten signature"></div>
  </main>
</body>
</html>
```